Personal Web page for recruiter and owner of consulting firm

I work full time as a recruiter so I want a page that allows for me to support my efforts. I would like a long single page, I need to be able to upload four two minute videos, and 4 images. I also want the color scheme to match with my consulting company. I own the domain marcusfenwold.net already through wordpress . I took a shot at it myself and its terrible.

Target Market(s)

Potential clients

Industry/Entity Type

Management Consulting

Logo Text

marcus fenwold

Font styles to use
Serif

Requirements
Must have
• Must in color scheme go well with my consulting company logo attached
• Must be able to upload 4 two minute videos and 4 images (photos of me)
• Single long scroll page
• Modern and clean
Nice to have
• Easy for me to update videos images and text without complex coding
Should not have
• I want the design and feel to go well with my logos not exactly replicate it

```html
<!DOCTYPE html>
<html lang="en">
<head>
<meta charset="utf-8">
<title>Marcus Fenwold — Fenwold Strategies</title>
<link href="https://fonts.googleapis.com/css2?family=Raleway:wght@300;400;600;700;800&family=Open+Sans:wght@400;600;700&display=swap" rel="stylesheet">
<style>
:root{
  --blue:#3b7cc0;
  --blue-dark:#2c62a0;
  --blue-light:#4f95da;
  --ink:#15171f;
  --ink-2:#23262f;
  --grey-bg:#ebebeb;
  --grey-text:#8a8a8a;
  --heading-dark:#3d3d3d;
  --white:#ffffff;
  --play:#e53935;
}
*{margin:0;padding:0;box-sizing:border-box}
html,body{width:1200px;height:4500px;overflow:hidden}
body{font-family:'Open Sans',Arial,sans-serif;color:var(--white);background:var(--ink)}
section,header,footer{position:relative;width:1200px;overflow:hidden}
.abs{position:absolute}
.center{left:0;right:0;text-align:center}
.photo{position:absolute;inset:0}

/* hero */
.hero{height:702px}
.hero .photo{background:radial-gradient(ellipse at 55% 45%,#4a4f63 0%,#2a2d3c 40%,#15161f 100%)}
.hero .photo::after{content:"";position:absolute;inset:0;background:linear-gradient(180deg,rgba(10,10,20,.35),rgba(20,16,28,.65))}
.brand{font-family:'Raleway',sans-serif;font-weight:400;letter-spacing:4px;color:var(--white);text-transform:uppercase;line-height:1.15}
.hero .brand{left:75px;top:44px;font-size:26px}
.nav{right:60px;top:66px;display:flex;gap:0}
.nav a{font-family:'Raleway',sans-serif;font-weight:700;font-size:13px;color:var(--white);text-decoration:none;letter-spacing:.5px;width:108px;text-align:center}
.hero-title{top:290px;font-family:'Raleway',sans-serif;font-weight:700;font-size:38px;letter-spacing:1px}
.hero-sub{top:345px;font-family:'Raleway',sans-serif;font-weight:300;font-size:30px}
.btn{display:inline-block;font-family:'Raleway',sans-serif;font-weight:700;font-size:12px;color:var(--white);background:var(--blue);border-radius:20px;padding:0;height:36px;line-height:36px;width:192px;text-align:center;text-decoration:none;letter-spacing:.5px}
.hero .btn{left:504px;top:412px;position:absolute}
.mouse{left:588px;top:608px}
.slide-dots{left:1158px;top:322px;display:flex;flex-direction:column;gap:17px}
.slide-dots i{width:7px;height:7px;border-radius:50%;background:rgba(255,255,255,.45)}
.slide-dots i:first-child{background:var(--white)}

/* about */
.about{height:610px;background:var(--blue)}
.about .brand{top:140px;font-size:40px;letter-spacing:5px}
.about .brand small{display:block;font-size:22px;letter-spacing:6px;margin-top:2px}
.about p{left:220px;right:220px;font-size:15.5px;line-height:33px;text-align:center}
.about .p1{top:265px}
.about .p2{top:405px}

/* services */
.services{height:660px}
.services .photo{background:linear-gradient(180deg,#3b3e47 0%,#2a2c33 50%,#1c1d23 100%)}
.services .photo::after{content:"";position:absolute;inset:0;background:radial-gradient(ellipse at 50% 40%,rgba(255,255,255,.08),rgba(0,0,0,.35))}
.section-title{font-family:'Raleway',sans-serif;font-weight:800;font-size:50px;letter-spacing:.5px}
.services .section-title{top:138px}
.intro{left:220px;right:220px;text-align:center;font-size:14px;line-height:30px}
.services .intro{top:208px}
.service{width:260px;text-align:center}
.service svg{display:block;margin:0 auto}
.service h3{font-family:'Raleway',sans-serif;font-weight:700;font-size:13px;color:var(--blue-light);margin-top:22px;letter-spacing:.5px}
.service p{font-size:13px;line-height:24px;margin-top:16px}
.carousel-dots{top:578px;left:0;right:0;display:flex;justify-content:center;gap:8px}
.carousel-dots i{width:6px;height:6px;border-radius:50%;background:rgba(255,255,255,.4)}
.carousel-dots i:first-child{background:var(--blue-light)}

/* videos */
.videos{height:1046px;background:var(--grey-bg)}
.videos .section-title{top:122px;color:var(--heading-dark)}
.videos .intro{top:190px;color:var(--grey-text);font-size:15px;line-height:33px}
.video{width:438px;height:288px;background:#111}
.video .frame{position:absolute;left:0;top:0;width:438px;height:252px}
.v1 .frame{background:linear-gradient(135deg,#c9ced6,#6b7480 55%,#2f3540)}
.v2 .frame{background:linear-gradient(135deg,#3b3f48,#7b6a62 50%,#1e2129)}
.v3 .frame{background:linear-gradient(135deg,#d7d2c9,#6b6e77 50%,#2c2f3b)}
.v4 .frame{background:linear-gradient(135deg,#a8b6c4,#dbe2ea 45%,#596577)}
.video .play{position:absolute;left:195px;top:102px}
.video .bar{position:absolute;left:0;bottom:0;width:438px;height:36px;background:#121212}

/* blog */
.blog{height:802px}
.blog .photo{background:linear-gradient(180deg,#22252f,#2f323c 50%,#1a1c24)}
.blog .photo::after{content:"";position:absolute;inset:0;background:rgba(12,14,22,.4)}
.blog .section-title{top:126px}
.blog .intro{top:192px;font-size:15px;line-height:33px}
.post{width:312px}
.post .pic{height:217px}
.post1 .pic{background:linear-gradient(135deg,#8b8f99,#c9b8a8 50%,#3c404a)}
.post2 .pic{background:linear-gradient(135deg,#5a5e68,#b9aea4 50%,#2b2e36)}
.post3 .pic{background:linear-gradient(135deg,#e5e0d6,#a89f93 50%,#59544d)}
.post h3{font-family:'Raleway',sans-serif;font-weight:700;font-size:14px;margin-top:25px}
.post .date{font-size:11px;margin-top:10px;opacity:.85}
.post p{font-size:12.5px;line-height:24px;margin-top:10px}

/* contact */
.contact{height:625px;background:var(--blue)}
.contact .section-title{top:140px}
.form{top:250px;left:150px;display:flex;gap:9px}
.field{width:216px;height:36px;border-radius:18px;background:var(--blue-dark);font-size:11px;line-height:36px;padding-left:22px;color:rgba(255,255,255,.7)}
.field+.field{margin-left:0}
.submit{width:216px;height:36px;border-radius:18px;border:1.5px solid var(--white);font-family:'Raleway',sans-serif;font-weight:700;font-size:11px;text-align:center;line-height:33px;margin-left:3px}
.info{width:300px;text-align:center;font-size:12px;color:rgba(255,255,255,.85)}
.info svg{display:block;margin:0 auto 22px}
.social{top:459px;left:507px;display:flex;gap:30px}
.social span{width:42px;height:42px;border-radius:50%;background:var(--blue-dark)}

footer{height:55px;background:var(--blue-dark);text-align:center;line-height:55px;font-size:12px;color:rgba(255,255,255,.8)}
</style>
</head>
<body>

<header class="hero">
  <div class="photo" role="img" aria-label="Photo of a hand using a tablet showing business charts"></div>
  <div class="abs brand">Marcus<br>Fenwold</div>
  <nav class="abs nav">
    <a href="#about">ABOUT</a><a href="#services">SERVICES</a><a href="#videos">VIDEOS</a><a href="#blog">BLOG</a><a href="#contact">CONTACT</a>
  </nav>
  <h1 class="abs center hero-title">FENWOLD STRATEGIES</h1>
  <p class="abs center hero-sub">I'm a full time recruiter and own a consulting firm.</p>
  <a class="btn" href="#contact">CONTACT HERE!</a>
  <svg class="abs mouse" width="24" height="44" viewBox="0 0 24 44" fill="none" stroke="#fff" stroke-width="1.6">
    <rect x="3" y="1" width="18" height="30" rx="9"/><line x1="12" y1="8" x2="12" y2="14"/><polyline points="8,36 12,40 16,36"/>
  </svg>
  <div class="abs slide-dots"><i></i><i></i><i></i><i></i></div>
</header>

<section class="about" id="about">
  <div class="abs center brand">Marcus Fenwold<small>Strategies</small></div>
  <p class="abs p1">Lorem Ipsum is simply dummy text of the printing and typesetting industry. Lorem Ipsum has been the industry's standard dummy text ever since the 1500s, when an unknown printer took a galley of type and scrambled it to make a type specimen book. It has survived not only five centuries</p>
  <p class="abs p2">Lorem Ipsum is simply dummy text of the printing and typesetting industry. Lorem Ipsum has been the industry's standard dummy text ever since the 1500s, when an unknown printer...</p>
</section>

<section class="services" id="services">
  <div class="photo" role="img" aria-label="Photo of business people walking through a busy hall"></div>
  <h2 class="abs center section-title">OUR SERVICES</h2>
  <p class="abs intro">Lorem Ipsum is simply dummy text of the printing and typesetting industry. Lorem Ipsum has been the industry's standard dummy text ever since the 1500s, when an unknown printer took a galley of type and scrambled...</p>

  <div class="abs service" style="left:155px;top:318px">
    <svg width="100" height="80" viewBox="0 0 100 80" fill="none" stroke="#fff" stroke-width="2.5">
      <circle cx="50" cy="14" r="8"/><path d="M36 36c2-8 8-12 14-12s12 4 14 12z"/>
      <circle cx="24" cy="48" r="7"/><path d="M12 68c2-7 7-10 12-10s10 3 12 10z"/>
      <circle cx="76" cy="48" r="7"/><path d="M64 68c2-7 7-10 12-10s10 3 12 10z"/>
      <line x1="10" y1="74" x2="90" y2="74"/>
    </svg>
    <h3>BUSINESS NETWORKS</h3>
    <p>Lorem Ipsum is simply dummy text of the printing and typesetting industry. Lorem Ipsum has been the industry...</p>
  </div>
  <div class="abs service" style="left:470px;top:318px">
    <svg width="100" height="80" viewBox="0 0 100 80" fill="none" stroke="#fff" stroke-width="2.5">
      <circle cx="48" cy="44" r="30"/><circle cx="48" cy="44" r="19"/><circle cx="48" cy="44" r="8"/>
      <line x1="48" y1="44" x2="80" y2="12"/><polyline points="72,8 80,12 84,4"/><polyline points="76,20 80,12 88,16"/>
    </svg>
    <h3>OPPORTUNITIES</h3>
    <p>Lorem Ipsum is simply dummy text of the printing and typesetting industry. Lorem Ipsum has been the industry...</p>
  </div>
  <div class="abs service" style="left:790px;top:318px">
    <svg width="100" height="80" viewBox="0 0 100 80" fill="none" stroke="#fff" stroke-width="2.5">
      <rect x="30" y="52" width="9" height="20"/><rect x="45" y="40" width="9" height="32"/><rect x="60" y="28" width="9" height="44"/><rect x="75" y="14" width="9" height="58"/>
    </svg>
    <h3>TRADING</h3>
    <p>Lorem Ipsum is simply dummy text of the printing and typesetting industry. Lorem Ipsum has been the industry...</p>
  </div>
  <div class="abs carousel-dots"><i></i><i></i><i></i></div>
</section>

<section class="videos" id="videos">
  <h2 class="abs center section-title">OUR VIDEOS</h2>
  <p class="abs intro">Lorem Ipsum is simply dummy text of the printing and typesetting industry. Lorem Ipsum has been the industry's standard dummy text ever since the 1500s</p>

  <div class="abs video v1" style="left:141px;top:323px">
    <div class="frame" role="img" aria-label="Video still of two colleagues working at a computer"></div>
    <svg class="play" width="48" height="48" viewBox="0 0 48 48"><circle cx="24" cy="24" r="24" fill="#e53935"/><polygon points="19,14 19,34 35,24" fill="#fff"/></svg>
    <div class="bar"><svg width="438" height="36" viewBox="0 0 438 36" fill="#fff"><polygon points="16,12 16,24 25,18"/><polygon points="36,15 40,15 45,11 45,25 40,21 36,21"/><rect x="390" y="13" width="10" height="10" fill="none" stroke="#fff" stroke-width="1.5"/><path d="M412 12h5v2h-3v3h-2zM426 12v5h-2v-3h-3v-2zM412 24v-5h2v3h3v2zM426 24h-5v-2h3v-3h2z"/></svg></div>
  </div>
  <div class="abs video v2" style="left:621px;top:323px">
    <div class="frame" role="img" aria-label="Video still of a woman speaking in an interview"></div>
    <svg class="play" width="48" height="48" viewBox="0 0 48 48"><circle cx="24" cy="24" r="24" fill="#e53935"/><polygon points="19,14 19,34 35,24" fill="#fff"/></svg>
    <div class="bar"><svg width="438" height="36" viewBox="0 0 438 36" fill="#fff"><polygon points="16,12 16,24 25,18"/><polygon points="36,15 40,15 45,11 45,25 40,21 36,21"/><rect x="390" y="13" width="10" height="10" fill="none" stroke="#fff" stroke-width="1.5"/><path d="M412 12h5v2h-3v3h-2zM426 12v5h-2v-3h-3v-2zM412 24v-5h2v3h3v2zM426 24h-5v-2h3v-3h2z"/></svg></div>
  </div>
  <div class="abs video v3" style="left:141px;top:653px">
    <div class="frame" role="img" aria-label="Video still of a business team shaking hands"></div>
    <svg class="play" width="48" height="48" viewBox="0 0 48 48"><circle cx="24" cy="24" r="24" fill="#e53935"/><polygon points="19,14 19,34 35,24" fill="#fff"/></svg>
    <div class="bar"><svg width="438" height="36" viewBox="0 0 438 36" fill="#fff"><polygon points="16,12 16,24 25,18"/><polygon points="36,15 40,15 45,11 45,25 40,21 36,21"/><rect x="390" y="13" width="10" height="10" fill="none" stroke="#fff" stroke-width="1.5"/><path d="M412 12h5v2h-3v3h-2zM426 12v5h-2v-3h-3v-2zM412 24v-5h2v3h3v2zM426 24h-5v-2h3v-3h2z"/></svg></div>
  </div>
  <div class="abs video v4" style="left:621px;top:653px">
    <div class="frame" role="img" aria-label="Video still of a consultant meeting a client at a laptop"></div>
    <svg class="play" width="48" height="48" viewBox="0 0 48 48"><circle cx="24" cy="24" r="24" fill="#e53935"/><polygon points="19,14 19,34 35,24" fill="#fff"/></svg>
    <div class="bar"><svg width="438" height="36" viewBox="0 0 438 36" fill="#fff"><polygon points="16,12 16,24 25,18"/><polygon points="36,15 40,15 45,11 45,25 40,21 36,21"/><rect x="390" y="13" width="10" height="10" fill="none" stroke="#fff" stroke-width="1.5"/><path d="M412 12h5v2h-3v3h-2zM426 12v5h-2v-3h-3v-2zM412 24v-5h2v3h3v2zM426 24h-5v-2h3v-3h2z"/></svg></div>
  </div>
</section>

<section class="blog" id="blog">
  <div class="photo" role="img" aria-label="Photo of a laptop on a desk in a dim office"></div>
  <h2 class="abs center section-title">BLOG POSTS</h2>
  <p class="abs intro">Lorem Ipsum is simply dummy text of the printing and typesetting industry. Lorem Ipsum has been the industry's standard dummy text ever since the 1500s</p>

  <article class="abs post post1" style="left:99px;top:330px">
    <div class="pic" role="img" aria-label="Photo of a presentation in a meeting room"></div>
    <h3>LOREM IPSUM IS SIMPLY DUMMY TEXT</h3>
    <div class="date">Posted on 27 march 2016</div>
    <p>Lorem Ipsum is simply dummy text of the printing and typesetting industry...</p>
  </article>
  <article class="abs post post2" style="left:444px;top:330px">
    <div class="pic" role="img" aria-label="Photo of colleagues reviewing a tablet"></div>
    <h3>LOREM IPSUM IS SIMPLY DUMMY TEXT</h3>
    <div class="date">Posted on 27 march 2016</div>
    <p>Lorem Ipsum is simply dummy text of the printing and typesetting industry...</p>
  </article>
  <article class="abs post post3" style="left:789px;top:330px">
    <div class="pic" role="img" aria-label="Photo of a team around a conference table seen from above"></div>
    <h3>LOREM IPSUM IS SIMPLY DUMMY TEXT</h3>
    <div class="date">Posted on 27 march 2016</div>
    <p>Lorem Ipsum is simply dummy text of the printing and typesetting industry...</p>
  </article>
</section>

<section class="contact" id="contact">
  <h2 class="abs center section-title">CONTACT</h2>
  <div class="abs form">
    <div class="field">Enter your name</div>
    <div class="field">Enter your Email id</div>
    <div class="field">Enter your Phone</div>
    <div class="submit">SUBMIT NOW</div>
  </div>

  <div class="abs info" style="left:205px;top:338px">
    <svg width="26" height="34" viewBox="0 0 26 34" fill="none" stroke="#fff" stroke-width="1.6"><path d="M13 32C6 22 2 17 2 12a11 11 0 0 1 22 0c0 5-4 10-11 20z"/><circle cx="13" cy="12" r="4"/></svg>
    123 Street name, city name, country - 0023536
  </div>
  <div class="abs info" style="left:477px;top:338px">
    <svg width="34" height="34" viewBox="0 0 34 34" fill="none" stroke="#fff" stroke-width="1.6"><path d="M8 3l5 7-3 4c2 4 6 8 10 10l4-3 7 5-3 5C16 31 3 18 3 6z"/><path d="M20 4a10 10 0 0 1 10 10M20 9a5 5 0 0 1 5 5"/></svg>
    + 555 (014) - 2290
  </div>
  <div class="abs info" style="left:753px;top:338px">
    <svg width="36" height="34" viewBox="0 0 36 34" fill="none" stroke="#fff" stroke-width="1.6"><rect x="2" y="7" width="32" height="20"/><polyline points="2,7 18,19 34,7"/></svg>
    hello@fenwoldstrategies.net
  </div>

  <div class="abs social" aria-label="Social links"><span></span><span></span><span></span></div>
</section>

<footer>Copyright © 2017. Fenwold Strategies. All rights reserved.</footer>

</body>
</html>
```